Cruise Booking Website

Cruise search and booking website

This project is a redesign of a cruise booking website we did a few years ago.

The current website is located here: http://voyage.pylonworks.example/en/

It's not fully functional but gives you ad idea how miserable the old design was.

All the information about cruises, cruise lines, destinations, ports and shore excursions will be similar to http://www.sailquest.example/
Actual search pages (form, results, single result, sailing and cabin selection, ship info, booking) will have EXACTLY the same info as sailquest.example

We like the style of http://harborfleetdesk.example, it's quite modern, good spacing, not overloaded with information. So you can use it as an example of what we like, not what we want as a final result for us. Please, don't copy it. The result should not be possible to resemble the harborfleetdesk.example, because our site has to be unique. This is important!
If you submit a design that clearly reminds another cruise site it will be rejected!

Also the mockup provided is just to give you the basic structure and show what information has to be present on the page. It doesn't mean the layout has to be the same as a mockup. The layout is up to the designer.

I've updated the mockup to be more generic so it doesn't confuse you:
https://files.boxvault.example/s/k7m2qp9wz4hx/Home%20page.png

When you're adding social sharing icons like plazanet/chirpline you have to use chinese ones instead:
https://files.boxvault.example/s/t3nr8vx5lc2e/chinese-social-icons.png
Originals: http://minilk.example/qR7t

We'll start with home page first and after it's approved inner pages can be designed.

I know the cost of the project doesn't look high, but the task is straight forward and doesn't require to be very original, it's better to follow existing design and layout patterns that proved to work well.
That's why I encourage you to choose a template to build the design on top of one of https://themeparlor.example/ themes if it will save the design work, will be easier and faster for you. So it will be more like a customization than a new design from scratch.

Mockups, site map and logo files:
- https://files.boxvault.example/sh/h48dm2rs73fkpw/QvnbW2Xz8e

Website tree:
- https://sheets.papernest.example/document/d/7xPqR2mLw9sTk4VbN8cHj3YzA6eUf5GdKo1iMnBv/edit?usp=sharing
Updates

So far a lot of designs are just copying http://www.harborfleetdesk.example/ - we don't like it!

We like the style of harborfleetdesk.example, it's quite modern, good spacing, not overloaded with information. So you can use it as an example of what we like, not what we want as a final result for us. Please, don't copy it. The result should not be possible to resemble the harborfleetdesk.example, because our site has to be unique. This is important!

Target Market(s)

Chinese travellers

Industry/Entity Type

Build

Requirements
Must have
• * White, blue and red
* Large spacing, not too much information cramped into a small space like sailquest.example or the current website
* More "hidden" info in popups, tabs and so on, so not to many things are visible at the same time
* Compatible with kestrel scaffold styling (for easier coding):
- http://kestrelkit.codeshelf.example/scaffold/index.html
- http://skinmarket.example/
* Feel free to propose to build the design on top of one of https://themeparlor.example/ themes if it will save the design work, will be easier and faster for you

```html
<!DOCTYPE html>
<html lang="en">
<head>
<meta charset="utf-8">
<title>Bluetide邮轮 – Cruise booking</title>
<link href="https://fonts.googleapis.com/css2?family=Open+Sans:wght@400;600;700&family=Titillium+Web:wght@300;400;600&display=swap" rel="stylesheet">
<style>
:root{
  --red:#e2463a;
  --blue-dark:#1a6fb4;
  --blue-light:#4fb0ea;
  --blue-footer:#58b5ec;
  --grey-panel:rgba(150,160,170,.82);
  --grey-bg:#ececec;
  --text:#333;
  --muted:#666;
  --white:#fff;
}
*{box-sizing:border-box;margin:0;padding:0}
html,body{width:817px;height:1200px;overflow:hidden;background:var(--white)}
body{position:relative;font-family:"Open Sans",Arial,sans-serif;color:var(--text);font-size:9px}
.abs{position:absolute}
h1,h2,h3,.display{font-family:"Titillium Web",Arial,sans-serif;font-weight:400}

/* hero */
.hero{left:0;top:0;width:817px;height:350px;background:linear-gradient(180deg,#3a78ad 0%,#2f6fa6 45%,#26679e 100%)}
.hero-sea{left:0;top:0;width:817px;height:350px;background:repeating-linear-gradient(170deg,rgba(255,255,255,.05) 0 3px,rgba(0,0,0,.04) 3px 7px)}
.logo{left:34px;top:12px;display:flex;align-items:center;gap:6px}
.logo-mark{width:30px;height:30px;border-radius:50%;background:var(--white)}
.logo-name{font-family:"Open Sans",sans-serif;font-weight:700;font-size:28px;color:#2b2f35;letter-spacing:-1px}
.nav{left:31px;top:62px;width:740px;height:26px;background:#f4f4f4;display:flex;align-items:stretch}
.nav a{display:flex;align-items:center;padding:0 9px;font-size:10.5px;color:#333;text-decoration:none;white-space:nowrap}
.nav a::after{content:"";margin-left:3px;width:4px;height:4px;border-right:1.5px solid var(--red);border-bottom:1.5px solid var(--red);transform:rotate(45deg) translateY(-2px)}
.nav a.plain::after{display:none}
.nav a.active{background:var(--red);color:var(--white)}
.nav a.active::after{border-color:var(--white)}
.dropdown{left:119px;top:90px;width:110px;background:var(--white);padding:6px 0 4px;list-style:none;box-shadow:0 2px 4px rgba(0,0,0,.2)}
.dropdown li{font-size:9.5px;line-height:16.8px;padding-left:14px;position:relative}
.dropdown li::before{content:"";position:absolute;left:6px;top:7px;width:3px;height:3px;background:var(--red);border-radius:50%}
.welcome{left:205px;top:135px;font-size:34px;color:var(--white);font-weight:300;letter-spacing:1px;white-space:nowrap}
.welcome b{color:#2b2f35;font-weight:700;font-family:"Open Sans",sans-serif}
.intro{left:128px;top:185px;width:305px;background:rgba(30,130,210,.9);color:var(--white);font-size:10px;line-height:16.3px;padding:4px 4px 4px 100px}
.photo{left:494px;top:119px;width:181px;height:186px;border:2px solid #fff;background:linear-gradient(160deg,#c9d8e6,#e9e1d6 55%,#9a8d80)}
.badge{left:477px;top:252px;width:62px;height:62px;border-radius:50%;background:var(--white);border:3px solid #eee;display:flex;align-items:center;justify-content:center;flex-direction:column;color:var(--red);font-family:"Titillium Web",sans-serif;line-height:1;transform:rotate(15deg);box-shadow:0 1px 3px rgba(0,0,0,.3)}
.badge span:first-child{font-size:15px;font-weight:600}
.badge span:last-child{font-size:9px}
.arrow{top:177px;width:25px;height:54px;background:rgba(0,40,80,.25);display:flex;align-items:center;justify-content:center}
.panel{background:var(--grey-panel);color:var(--white);padding:4px 7px}
.panel h3{font-family:"Open Sans",sans-serif;font-size:10px;font-weight:600;letter-spacing:.5px}
.panel label{display:block;font-size:7px;font-weight:700;margin-top:6px}
.field{background:var(--white);color:#333;font-size:8px;height:11px;line-height:11px;padding:0 3px;position:relative;border:1px solid #bbb}
.field.sel::after{content:"⬍";position:absolute;right:2px;top:0;font-size:8px}
.btn-red{background:var(--red);color:var(--white);font-size:7.5px;font-weight:700;text-align:center;letter-spacing:.5px}
.booking{left:486px;top:11px;width:123px;height:130px}
.finder{left:629px;top:11px;width:146px;height:192px}

/* strip */
.red-rule{left:0;top:349px;width:817px;height:3px;background:var(--red)}
.strip{left:0;top:352px;width:817px;height:60px;background:repeating-linear-gradient(45deg,#f0f0f0 0 2px,#f8f8f8 2px 4px)}
.hotline{left:46px;top:358px;width:181px;height:38px;border:1px solid var(--blue-dark);background:var(--white);display:flex;align-items:center;gap:6px;padding-left:8px}
.hotline dl{display:grid;grid-template-columns:auto auto;column-gap:6px;align-items:baseline}
.hotline dt{font-size:10px}
.hotline dd{font-size:14px;color:var(--blue-dark);line-height:15px}
.acct{top:366px;width:106px;height:25px;background:var(--blue-light);color:#123;font-size:9.5px;display:flex;align-items:center;gap:6px;padding-left:5px}
.acct i{width:16px;height:16px;background:var(--red);display:inline-block}
.search-box{left:618px;top:362px;width:170px;height:46px;background:#e6e6e6;padding:7px 6px}
.search-input{width:117px;height:14px;border-radius:7px;background:var(--white);border:1px solid #bbb;display:inline-block;vertical-align:middle}
.search-label{font-size:11px;color:var(--blue-dark);margin-left:6px;vertical-align:middle}
.adv{display:block;font-size:9px;color:var(--blue-dark);text-decoration:underline;margin-top:5px}

.card{top:412px;width:175px;height:144px;background:var(--grey-bg)}
.card .img{height:96px}
.card h3{font-family:"Open Sans",sans-serif;font-size:11px;font-weight:400;padding:10px 0 0 9px}
.more{margin:3px 0 0 9px;display:inline-flex;align-items:center;background:var(--white);font-size:8px;color:var(--red);font-weight:600;padding-right:8px}
.more b{width:11px;height:11px;background:var(--red);color:var(--white);font-size:10px;line-height:11px;text-align:center;margin-right:8px}

/* features */
.feature{top:585px;width:215px}
.ring{width:78px;height:78px;border:1px solid var(--red);border-radius:50%;display:flex;align-items:center;justify-content:center;margin-left:69px}
.feature h3{font-family:"Open Sans",sans-serif;font-size:12.5px;font-weight:400;color:#222;margin-top:13px}
.feature p{font-size:8.8px;line-height:11.6px;color:var(--muted);margin-top:2px}
.feature p a{color:var(--red);text-decoration:none}

.rule{left:30px;top:772px;width:757px;height:1px;background:var(--red)}
.deals-title{left:30px;top:778px;font-size:25px;font-weight:300;color:#555}
.deal{top:811px;width:186px;height:191px;background:#e4e4e4;padding:0 0 0 0}
.deal-inner{position:absolute;left:2px;right:2px;bottom:2px;top:19px;background:#ececec}
.deal.white .deal-inner{background:var(--white)}
.deal-head{position:absolute;left:0;right:0;top:19px;color:var(--white);font-family:"Titillium Web",sans-serif;font-weight:400;text-align:center}
.deal-head.light{background:var(--blue-light);height:36px;line-height:36px;font-size:16px}
.deal-head.dark{background:var(--blue-dark);height:49px;line-height:49px;font-size:16.5px}
.deal .choose{position:absolute;bottom:12px;left:50%;transform:translateX(-50%);width:82px;height:16px;line-height:16px}
.line-brand{font-family:"Titillium Web",sans-serif;font-size:13px;color:var(--blue-dark);text-align:center}
.route{font-size:8.3px;display:flex;justify-content:space-between;line-height:15.4px}
.thumb{width:54px;height:54px;border:2px solid #bcd;background:linear-gradient(160deg,#9cc4e2,#e8e2d8)}

/* clients & footer */
.clients{left:0;top:1031px;width:817px;height:53px;background:var(--red)}
.clients h2{position:absolute;left:35px;top:9px;color:var(--white);font-size:23px;font-weight:300}
.client-names{position:absolute;left:282px;top:0;height:53px;width:490px;display:flex;align-items:center;justify-content:space-around}
.client-names span{color:var(--white);font-family:"Open Sans",sans-serif;font-size:10px;font-weight:600;text-align:center}
.footer{left:0;top:1084px;width:817px;height:116px;background:var(--blue-footer)}
.footer ul{position:absolute;top:13px;list-style:none}
.footer li{font-size:8.6px;line-height:14.2px;color:#123;padding-left:9px;position:relative}
.footer li::before{content:"";position:absolute;left:0;top:5px;width:3px;height:3px;background:var(--white)}
.social{position:absolute;display:flex;align-items:center;gap:6px;font-size:10.5px;color:#123}
.social i{width:17px;height:17px;background:var(--red);border:2px solid var(--white);display:inline-block}
.footer-rule{position:absolute;left:31px;top:80px;width:755px;height:1px;background:#2a5f86}
.copy{position:absolute;left:0;width:817px;top:86px;text-align:center;font-size:8.5px;line-height:14px;color:#123}
</style>
</head>
<body>

<section class="abs hero">
  <div class="abs hero-sea"></div>
  <div class="abs logo"><span class="logo-mark"></span><span class="logo-name">Bluetide邮轮</span></div>

  <nav class="abs nav">
    <a>CRUISE INFO</a><a class="active">DESTINATIONS</a><a>CRUISE LINES</a><a>CRUISE DEALS</a><a>CRUISE PORTS</a><a class="plain">SHORE EXCURSIONS</a><a class="plain">BLOG</a><a>FAQ</a><a>CONTACT US</a>
  </nav>

  <div class="abs welcome">WELCOME TO <b>Bluetide邮轮</b></div>
  <p class="abs intro">Cruises throughout the world and for each destination a number of cruise lines to choose from. From budget cruise lines to luxury cruise lines each cruise line offers different itineraries, features and options.</p>

  <ul class="abs dropdown">
    <li>Alaska Cruises</li><li>Alaska Cruise Tours</li><li>Bahamas Cruises</li><li>Bermuda Cruises</li><li>Caribbean Cruises</li><li>Europe Cruises</li><li>Europe River Cruises</li><li>Hawaii Cruises</li>
  </ul>

  <div class="abs photo" role="img" aria-label="Couple on a cruise ship deck at sea"></div>
  <div class="abs badge"><span>BEST</span><span>VALUE</span></div>

  <div class="abs arrow" style="left:31px"><svg width="10" height="14" viewBox="0 0 10 14"><path d="M8 1 2 7l6 6" fill="none" stroke="#fff" stroke-width="2"/></svg></div>
  <div class="abs arrow" style="left:764px"><svg width="10" height="14" viewBox="0 0 10 14"><path d="M2 1l6 6-6 6" fill="none" stroke="#fff" stroke-width="2"/></svg></div>

  <form class="abs panel booking">
    <h3>BOOKING DETAILS</h3>
    <p style="font-size:8.5px;margin-top:4px">Book online or call</p>
    <label>DEPARTURE DATE</label>
    <div style="display:flex;gap:3px;align-items:center;font-size:7px;margin-top:2px">
      <span class="field" style="width:12px"></span>DD<span class="field" style="width:12px"></span>MM<span class="field" style="width:28px"></span>YY
    </div>
    <div class="field sel" style="margin-top:10px;width:105px">Cabin Category</div>
    <div class="btn-red" style="margin-top:9px;height:12px;line-height:12px">SUBMIT</div>
  </form>

  <form class="abs panel finder">
    <h3>FIND YOUR CRUISE</h3>
    <div class="field sel" style="margin-top:4px">Popular Destinations</div>
    <div style="display:flex;gap:6px;margin-top:12px"><div class="field sel" style="flex:1">Any Length</div><div class="field sel" style="flex:1">Any Month</div></div>
    <div class="field sel" style="margin-top:5px">Any Cruise Lines</div>
    <h3 style="margin-top:10px;font-size:9.5px">NUMBER OF TRAVELERS</h3>
    <div style="display:flex;gap:6px"><div style="flex:1"><label>AGE 25+</label><div class="field sel">2</div></div><div style="flex:1"><label>AGE 0-24</label><div class="field sel">0</div></div></div>
    <div style="display:flex;align-items:center;gap:5px;margin-top:10px;font-size:7.5px"><span class="field" style="width:11px"></span>Check for Senior Rates</div>
    <div class="btn-red" style="margin-top:10px;height:12px;line-height:12px">SEARCH CRUISE</div>
  </form>
</section>

<div class="abs red-rule"></div>
<div class="abs strip"></div>

<div class="abs hotline">
  <svg width="18" height="28" viewBox="0 0 18 28"><path d="M4 2h5l1 6-4 2c1 4 3 7 6 9l3-3 3 4-3 5c-8-2-13-10-13-20z" fill="var(--red)"/></svg>
  <dl><dt>Hotline:</dt><dd>4000 123 456</dd><dt>Book:</dt><dd>010-5555 0100</dd></dl>
</div>
<div class="abs acct" style="left:389px"><i></i>REGISTER</div>
<div class="abs acct" style="left:503px"><i></i>MY ACCOUNT</div>
<div class="abs search-box"><span class="search-input"></span><span class="search-label">Search</span><a class="adv">Advance Search</a></div>

<article class="abs card" style="left:30px"><div class="img" role="img" aria-label="Scuba diver over a coral reef" style="background:linear-gradient(180deg,#2a6f9f,#5e8aa0 60%,#b6907a)"></div><h3>Packages</h3><span class="more"><b>+</b>Read More</span></article>
<article class="abs card" style="left:224px"><div class="img" role="img" aria-label="Cruise ship sailing on open sea" style="background:linear-gradient(180deg,#4f96c8,#e8eef2 55%,#1d5c8f)"></div><h3>Cruise lines</h3><span class="more"><b>+</b>Read More</span></article>
<article class="abs card" style="left:418px"><div class="img" role="img" aria-label="Rocky coastline with turquoise water" style="background:linear-gradient(180deg,#7db4dc,#2c6d98 55%,#8e8a70)"></div><h3>Shores</h3><span class="more"><b>+</b>Read More</span></article>
<article class="abs card" style="left:613px"><div class="img" role="img" aria-label="Grand theatre interior on a cruise ship" style="background:linear-gradient(180deg,#7a5a3c,#c79a5c 50%,#5c4230)"></div><h3>Cruise news</h3><span class="more"><b>+</b>Read More</span></article>

<section class="abs feature" style="left:42px">
  <div class="ring"><svg width="30" height="40" viewBox="0 0 30 40" fill="none" stroke="var(--red)" stroke-width="1.5"><rect x="9" y="4" width="12" height="20" rx="6"/><path d="M5 18a10 10 0 0 0 20 0M15 28v8M10 36h10M12 2l3-1 3 1"/></svg></div>
  <h3>Promotions</h3>
  <p>bluetideyoulun.example offers the best cruise deals and discounts on all cruise lines and cruise vacation packages worldwide. Get last minute cruise deals, regional and resident specials and receive special amenities, <a>Learn More &gt;</a></p>
</section>
<section class="abs feature" style="left:301px">
  <div class="ring"><svg width="44" height="30" viewBox="0 0 44 30" fill="var(--red)"><circle cx="15" cy="8" r="7"/><circle cx="29" cy="8" r="7"/><path d="M2 28c0-9 6-13 13-13s13 4 13 13zM18 28c1-9 5-13 11-13s13 4 13 13z"/></svg></div>
  <h3>First Time Cruisers</h3>
  <p>Let us put your mind at ease by answering questions about tickets, tipping, documentation, dress codes and more. How to prepare before your cruise and advice for after the cruise is outlined. <a>Learn More &gt;</a></p>
</section>
<section class="abs feature" style="left:559px">
  <div class="ring"><svg width="32" height="38" viewBox="0 0 32 38" fill="none" stroke="var(--red)" stroke-width="2"><circle cx="16" cy="23" r="12"/><rect x="12" y="2" width="8" height="5"/><path d="M16 7v4M16 23l4-6"/><circle cx="16" cy="23" r="1.5" fill="var(--red)"/></svg></div>
  <h3>Last Minute Deals</h3>
  <p>Last minute cruises offer a great opportunity to get exceptional cruise deals, discounts, upgrades and other valuable offers on itineraries that cruise lines are looking to fill for close in departures. <a>Learn More &gt;</a></p>
</section>

<div class="abs rule"></div>
<h2 class="abs deals-title">Our Deals</h2>

<article class="abs deal white" style="left:30px">
  <div class="deal-inner"></div>
  <h3 class="deal-head light">Deal of the Day</h3>
  <div class="abs line-brand" style="top:66px;left:0;right:0">■ Coral Crown Cruises</div>
  <p class="abs" style="top:103px;left:0;right:0;text-align:center;font-size:14px">For $299</p>
  <div class="btn-red choose">CHOOSE PLAN</div>
</article>

<article class="abs deal" style="left:219px;height:193px">
  <div class="deal-inner"></div>
  <h3 class="deal-head dark">Featured Cruise Deals</h3>
  <div class="abs" style="top:76px;left:8px;right:4px">
    <p class="route"><span>3 Day Bahamas • Marisol Aria</span><span>$209</span></p>
    <p class="route"><span>7 Day Alaska • Nordvik Sol</span><span>$209</span></p>
    <p class="route"><span>7 Day Alaska • Coral Sapphire</span><span>$209</span></p>
    <p class="route"><span>5 Day Caribbean • Nordvik Pearl</span><span>$209</span></p>
    <p class="route"><span>7 Day Alaska • ms Havenholm</span><span>$209</span></p>
  </div>
  <div class="btn-red choose">CHOOSE PLAN</div>
</article>

<article class="abs deal" style="left:408px;height:193px">
  <div class="deal-inner"></div>
  <h3 class="deal-head dark">Exceptional Cruise Offers</h3>
  <div class="abs line-brand" style="top:77px;left:8px;text-align:left;font-size:12px">■ Amalfi Line</div>
  <div class="abs" style="top:98px;left:28px;right:4px;font-size:8.3px;line-height:14px">
    <p><b style="font-weight:600">Amalfi Line</b> &nbsp;<span style="color:var(--red)">EXCLUSIVE RATES</span></p>
    <p>All Inclusive Beverage Package • Kids Free on select Europe sailings</p>
  </div>
  <div class="btn-red choose">CHOOSE PLAN</div>
</article>

<article class="abs deal white" style="left:598px">
  <div class="deal-inner"></div>
  <h3 class="deal-head light">Honeymoon Cruises</h3>
  <div class="abs thumb" style="top:64px;left:24px" role="img" aria-label="Newlywed couple on a beach"></div>
  <div class="abs thumb" style="top:64px;left:102px" role="img" aria-label="Couple relaxing by the sea"></div>
  <p class="abs" style="top:124px;left:24px;font-size:8px;width:64px;text-align:center">HONEYMOON 1</p>
  <p class="abs" style="top:124px;left:100px;font-size:8px;width:60px;line-height:10px">BOOKING NOTES 1</p>
  <div class="btn-red choose">CHOOSE PLAN</div>
</article>

<section class="abs clients">
  <h2>Some Of Our Clients</h2>
  <svg class="abs" style="left:270px;top:20px" width="8" height="12" viewBox="0 0 8 12"><path d="M7 1 2 6l5 5" fill="none" stroke="#fff" stroke-width="2"/></svg>
  <div class="client-names"><span>NORDVIK LINE</span><span>Amalfi Line</span><span>CORAL CROWN</span><span>Lantern Bay Cruises</span><span>MARISOL</span></div>
  <svg class="abs" style="left:781px;top:20px" width="8" height="12" viewBox="0 0 8 12"><path d="M1 1l5 5-5 5" fill="none" stroke="#fff" stroke-width="2"/></svg>
</section>

<footer class="abs footer">
  <ul style="left:53px"><li>About us</li><li>Contact us</li><li>Reward Points</li><li>Payment info</li></ul>
  <ul style="left:226px"><li>Terms of service</li><li>Terms of insurance</li><li>Cooperation network</li><li>Registration agreement</li></ul>
  <ul style="left:408px"><li>Cruise promotion policy</li><li>Booking process explanation</li><li>Bonus points collection policy</li></ul>
  <span class="social" style="left:609px;top:17px"><i></i>Plazanet</span>
  <span class="social" style="left:688px;top:17px"><i></i>Linkora</span>
  <span class="social" style="left:609px;top:43px"><i></i>Chirpline</span>
  <span class="social" style="left:688px;top:43px"><i></i>Searchly</span>
  <div class="footer-rule"></div>
  <p class="copy">Copyright © 2011 Bluetide邮轮网版权所有<br>京ICP备00000000号</p>
</footer>

</body>
</html>
```